Design and Renovation Company Luxury Business Card

I want to create a luxury business card for a Design and Renovation Firm . We will use our current logo. The company name is 528BUILDA. We do not want anything standard. We need a very unique concept.
Please see uploaded inspiration. I really like the textured paper option. I would like the card to be thick with debossing, and/or embossing options. The logo has orange in it but I would like to see the card with and without the orange. I think the orange may make the company feel less high-end. The goal is to elevate the logo not match its vibe per se of the logo. We want something very unique, not standard at all!
I would like a space for :
Logo,
Name,
Position,
Email,
Office number,
Website Address,
Business Address,
Thank you!
Have fun!
Target Market(s)
Home owners Age 35 +
Industry/Entity Type
Design and Renovation
Contact Information for Business Card
Logo, Name, Position, Email, Office number, Website Address, Business Address,.
Colors
Designer to choose colors to be used in the design.
Requirements
Must have
- A luxury designer feel. Must be black or dark grey but open to other luxury ideas.
Nice to have
- Gold, silver, black embossing or debossing. Textured paper design.
Should not have
- A cheap look and feel.

```html
<!DOCTYPE html>
<html lang="en">
<head>
<meta charset="utf-8">
<title>528BUILDA Business Card</title>
<link href="https://fonts.googleapis.com/css2?family=Arimo:wght@400;700&display=swap" rel="stylesheet">
<style>
  :root {
    --backdrop: #9b9b9b;
    --card-front: #2e2e2e;
    --card-back: #272727;
    --accent: #f0931f;
    --paper-white: #f3f3f3;
    --text-light: #e9e9e9;
  }
  * { box-sizing: border-box; margin: 0; padding: 0; }
  html, body { width: 1200px; height: 1050px; overflow: hidden; }
  body {
    background: var(--backdrop);
    font-family: "Arimo", Arial, sans-serif;
    position: relative;
  }
  .card {
    position: absolute;
    left: 290px;
    width: 620px;
    height: 354px;
    border-radius: 22px;
    overflow: hidden;
  }
  .card--front { top: 150px; background: var(--card-front); }
  .card--back { top: 560px; background: var(--card-back); }
  .paper-texture { position: absolute; inset: 0; width: 100%; height: 100%; opacity: 0.22; }

  /* Front face content is set in a portrait column turned to read upward */
  .front-layout {
    position: absolute;
    left: 133px;
    top: -133px;
    width: 354px;
    height: 620px;
    transform: rotate(-90deg);
    display: flex;
    flex-direction: column;
    align-items: center;
    color: var(--text-light);
    text-align: center;
  }
  .brand-mark {
    margin-top: 70px;
    display: flex;
    align-items: center;
    gap: 12px;
  }
  .brand-mark__square { width: 22px; height: 22px; background: var(--accent); }
  .brand-mark__name {
    font-size: 30px;
    font-weight: 700;
    letter-spacing: 2px;
    color: var(--paper-white);
  }
  .person-name {
    margin-top: 58px;
    font-size: 22px;
    font-weight: 700;
    color: var(--accent);
  }
  .person-role { margin-top: 2px; font-size: 14px; }
  .contact-icons {
    margin-top: 24px;
    display: flex;
    align-items: center;
    gap: 6px;
  }
  .contact-icons__rule { width: 10px; height: 1px; background: var(--text-light); }
  .contact-icons svg { width: 18px; height: 18px; display: block; }
  .contact-list { margin-top: 14px; font-size: 13.5px; line-height: 18px; }
  .section-rule { margin-top: 26px; width: 88px; height: 1px; background: var(--text-light); }
  .address { margin-top: 26px; font-size: 13.5px; line-height: 18px; }

  .back-layout {
    position: absolute;
    inset: 0;
    display: flex;
    align-items: center;
    justify-content: center;
    gap: 18px;
  }
  .back-layout .brand-mark__square { width: 40px; height: 40px; }
  .back-layout .brand-mark__name { font-size: 48px; letter-spacing: 5px; }
</style>
</head>
<body>
  <svg width="0" height="0" style="position:absolute">
    <filter id="paper-grain">
      <feTurbulence type="fractalNoise" baseFrequency="0.9" numOctaves="3" result="noise"/>
      <feColorMatrix type="saturate" values="0"/>
    </filter>
  </svg>

  <section class="card card--front">
    <svg class="paper-texture" aria-hidden="true"><rect width="100%" height="100%" filter="url(#paper-grain)"/></svg>
    <div class="front-layout">
      <div class="brand-mark">
        <span class="brand-mark__square"></span>
        <span class="brand-mark__name">528BUILDA</span>
      </div>
      <p class="person-name">Daniel Hart</p>
      <p class="person-role">President</p>
      <div class="contact-icons">
        <span class="contact-icons__rule"></span>
        <svg viewBox="0 0 18 18" aria-label="Phone"><circle cx="9" cy="9" r="9" fill="var(--accent)"/><path d="M6 4.5l1.6 2.2-1 1c.6 1.3 1.6 2.3 2.9 2.9l1-1 2.2 1.6-.8 1.6c-3.6-.4-6.5-3.3-6.9-6.9z" fill="#fff"/></svg>
        <svg viewBox="0 0 18 18" aria-label="Email"><circle cx="9" cy="9" r="9" fill="var(--accent)"/><rect x="4.5" y="5.8" width="9" height="6.4" fill="none" stroke="#fff" stroke-width="1.1"/><path d="M4.8 6.2L9 9.4l4.2-3.2" fill="none" stroke="#fff" stroke-width="1.1"/></svg>
        <svg viewBox="0 0 18 18" aria-label="Website"><circle cx="9" cy="9" r="9" fill="var(--accent)"/><circle cx="9" cy="9" r="4.5" fill="none" stroke="#fff" stroke-width="1.1"/><ellipse cx="9" cy="9" rx="2" ry="4.5" fill="none" stroke="#fff" stroke-width="1"/><path d="M4.5 9h9" stroke="#fff" stroke-width="1"/></svg>
        <span class="contact-icons__rule"></span>
      </div>
      <div class="contact-list">
        <p>(482) 5190-3374</p>
        <p>name@528BUILDA.com</p>
        <p>www.528BUILDA.com</p>
      </div>
      <span class="section-rule"></span>
      <div class="address">
        <p>6127 Ashbury Lane</p>
        <p>Glen Harbor, NY 11042</p>
      </div>
    </div>
  </section>

  <section class="card card--back">
    <div class="back-layout">
      <span class="brand-mark__square"></span>
      <span class="brand-mark__name">528BUILDA</span>
    </div>
  </section>
</body>
</html>
```